New business card/stationary for a consulting company

I am looking for a clean and very professional looking business card for my consulting company as well as corresponding stationary. I am uploading our logo. I like simple and powerful for the feel. No graphics but I am open on everything else. Below is my contact information but would like the final to be in a version I can add my employees information into and print. Thank you.

Daniel Whitcombe
dan@ferncliffadvisory.com
2870 North 9th Avenue, Summit Floor, Elm Ridge, Illinois 60531
www.ferncliffadvisory.com

Industry/Entity Type

Consulting

Contact Information for Business Card

Daniel Whitcombe
dan@ferncliffadvisory.com
www.ferncliffadvisory.com

Font styles to use
Serif
Sans Serif

Requirements
Must have
• Our logo and the business card details.
Nice to have
• our website www.ferncliffadvisory.com

```html
<!DOCTYPE html>
<html lang="en">
<head>
<meta charset="utf-8">
<title>Ferncliff Advisory – Business Card</title>
<link rel="stylesheet" href="https://fonts.googleapis.com/css2?family=Questrial&family=Open+Sans:wght@400&display=swap">
<style>
  :root {
    --navy: #05056b;
    --frost: #f3f1f1;
    --frost-edge: #e6e3e3;
    --backdrop: #e9e6e4;
    --silver: #d9d9e3;
    --white: #ffffff;
    --ghost: #8d8cc0;
  }
  * { margin: 0; padding: 0; box-sizing: border-box; }
  html, body { width: 1200px; height: 900px; overflow: hidden; }
  body { background: var(--backdrop); position: relative; font-family: "Questrial", sans-serif; }

  .card {
    position: absolute;
    background: linear-gradient(180deg, var(--frost) 0%, var(--frost-edge) 100%);
    box-shadow: 0 2px 10px rgba(0,0,0,0.08);
    overflow: hidden;
  }
  .card-front { left: 178px; top: 74px; width: 588px; height: 364px; }
  .card-back  { left: 388px; top: 505px; width: 567px; height: 352px; }

  .rule { position: absolute; left: 0; right: 0; background: var(--navy); }
  .band { position: absolute; left: 0; right: 0; bottom: 0; background: var(--navy); }

  .card-front .rule { top: 196px; height: 7px; }
  .card-front .band { top: 209px; }
  .card-back .rule  { top: 190px; height: 7px; }
  .card-back .band  { top: 202px; }

  .brand {
    position: absolute; left: 0; right: 0;
    display: flex; align-items: center; justify-content: center; gap: 14px;
    color: var(--navy);
    font-family: "Questrial", sans-serif;
    font-size: 26px; letter-spacing: 1.5px; text-transform: uppercase;
  }
  .brand-mark { width: 18px; height: 18px; background: currentColor; }
  .card-front .brand { top: 122px; }
  .card-back .brand { top: 120px; color: var(--ghost); transform: scaleX(-1); }

  .holder-name {
    position: absolute; top: 236px; left: 0; right: 0; text-align: center;
    color: var(--white); font-size: 19px; letter-spacing: 1.2px; text-transform: uppercase;
  }
  .contact {
    position: absolute; top: 272px; left: 0; right: 0;
    display: flex; justify-content: center;
    color: var(--white); font-family: "Open Sans", sans-serif; font-size: 14.5px; line-height: 22px;
  }
  .contact-online { text-align: right; padding-right: 14px; border-right: 1px solid var(--white); }
  .contact-online li { list-style: none; display: flex; align-items: center; justify-content: flex-end; gap: 6px; }
  .contact-online svg { width: 13px; height: 13px; fill: var(--white); }
  .contact-address { padding-left: 20px; font-style: normal; }
</style>
</head>
<body>
  <section class="card card-front" aria-label="Business card front">
    <div class="brand"><span class="brand-mark"></span>Ferncliff Advisory</div>
    <div class="rule"></div>
    <div class="band"></div>
    <p class="holder-name">Daniel Whitcombe</p>
    <div class="contact">
      <ul class="contact-online">
        <li>dan@ferncliffadvisory.com
          <svg viewBox="0 0 16 16" aria-hidden="true"><path d="M1 3h14v10H1z M2 4v.4l6 4.2 6-4.2V4z" fill-rule="evenodd"/></svg>
        </li>
        <li>www.ferncliffadvisory.com
          <svg viewBox="0 0 16 16" aria-hidden="true"><circle cx="8" cy="8" r="7"/><path d="M4 6c2-1 3 1 4 0s1-3 3-2M6 12c1-2 3-1 4-3" stroke="#05056b" stroke-width="1.3" fill="none"/></svg>
        </li>
      </ul>
      <address class="contact-address">2870 North 9th Avenue,<br>Summit Floor, Elm Ridge,<br>Illinois 60531</address>
    </div>
  </section>

  <section class="card card-back" aria-label="Business card back">
    <div class="brand" aria-hidden="true"><span class="brand-mark"></span>Ferncliff Advisory</div>
    <div class="rule"></div>
    <div class="band"></div>
  </section>
</body>
</html>
```